lantern pathway for children needs a website designer

We need a website designer for our new extension to our company known as 'lantern pathway' providing shadow support services to children based in Singapore. We are a sister branch of a private clinic 'Bright horizons' providing speech language, occupational, and educational therapy to children.

We would like to use our own photos. So the selected design should have a frame with pictures to give us an idea but we will replace them with our own. We will be needing help with inputting information and changing information throughout.

We would like to see designs that are simple, and professional. We have a logo (see attached). The result should convey professionalism in shadow support, fostering independent thinking and moving students towards self-learning.

Target Market(s)

Teachers, psychologists, parents

Industry/Entity Type

Clinic

Requirements
Should not have
• too distracting colours

```html
<!DOCTYPE html>
<html lang="en">
<head>
<meta charset="utf-8">
<title>Lantern Pathway – Shadow Support</title>
<link href="https://fonts.googleapis.com/css2?family=Open+Sans:wght@400;600&display=swap" rel="stylesheet">
<style>
:root{
  --brand:#7d0a0a;
  --brand-bright:#9b0f0f;
  --ink:#333;
  --muted:#777;
  --page:#dcdad8;
  --panel:#fff;
  --band:#acacac;
  --band-light:#dddbdb;
  --field:#f3f3f3;
}
*{margin:0;padding:0;box-sizing:border-box}
html,body{width:672px;height:1200px;overflow:hidden}
body{font-family:"Open Sans",Arial,sans-serif;background:var(--page);color:var(--ink);position:relative}
.abs{position:absolute}
.site-header{left:0;top:0;width:672px;height:70px;background:var(--panel)}
.brand-name{left:107px;top:20px;font-size:23px;font-weight:600;color:var(--brand);letter-spacing:-.3px}
.header-action{width:50px;text-align:center;font-size:5px;color:var(--ink);top:28px}
.header-action .dot{display:block;width:32px;height:32px;border-radius:50%;background:var(--brand);margin:0 auto 3px;position:relative;top:-16px}
.header-action svg{position:absolute;left:8px;top:8px}
.header-action span{position:relative;top:-16px}
.main-nav{left:0;top:70px;width:672px;height:40px;background:var(--brand)}
.nav-item{top:0;height:40px;line-height:40px;font-size:6.4px;color:#fff;text-transform:uppercase;transform:translateX(-50%);white-space:nowrap}
.nav-home{left:131px;top:0;width:54px;height:40px;background:var(--brand-bright);border-bottom:3px solid #d8d8d8}
.content-panel{left:106px;top:110px;width:459px;height:720px;background:var(--panel)}
.hero{left:106px;top:110px;width:459px;height:224px;background:linear-gradient(100deg,#e9e6e2 0%,#cfd3d6 35%,#b9bfc3 55%,#e7d8b0 75%,#d9a39a 100%)}
.slider-tab{left:484px;top:324px;width:69px;height:15px;background:#8a8a8a;border-radius:2px;box-shadow:1px 1px 2px rgba(0,0,0,.4)}
.slider-tab i{display:inline-block;width:10px;height:10px;border-radius:50%;background:#fff;margin:2.5px 1px 0 2.5px}
.drop{width:32px;height:32px;border-radius:50%;background:var(--brand);color:#fff;text-align:center;font-size:24px;line-height:32px;box-shadow:-3px 3px 4px rgba(0,0,0,.3)}
.heading{font-size:13.5px;color:var(--brand);text-transform:uppercase;letter-spacing:-.3px;white-space:nowrap}
.sub{font-size:5px;color:var(--ink);white-space:nowrap}
.copy{font-size:6.3px;line-height:9.1px;text-align:justify;color:var(--ink)}
.copy b{font-weight:400;color:var(--brand)}
.service-photo{width:56px;height:56px;border-radius:50%;border:3px solid #c8c8c8}
.service-label{font-size:6.4px;color:var(--brand);text-align:center;width:120px}
.num{width:18px;height:18px;border-radius:50%;background:var(--brand);color:#fff;font-size:8px;line-height:18px;text-align:center;box-shadow:-2px 2px 3px rgba(0,0,0,.3)}
.q-title{font-size:7.6px;color:var(--muted);line-height:8px}
.q-body{font-size:5.1px;line-height:7.4px;text-align:justify;color:var(--ink)}
.enquiry-band{left:0;top:830px;width:672px;height:127px;background:var(--band)}
.field-label{font-size:6px;color:#333;text-transform:uppercase}
.field{background:var(--field);border:1px solid #e6e6e6}
.submit{left:425px;top:917px;width:47px;height:19px;background:var(--brand);color:#fff;font-size:7.5px;line-height:19px;text-align:center}
.testimonial-band{left:0;top:957px;width:672px;height:130px;background:var(--band-light)}
.quote{font-size:6.3px;line-height:10.5px;text-align:justify;color:var(--ink);width:164px}
.quote-mark{font-size:14px;font-weight:600;color:#444;line-height:10px}
.author{font-size:7px;color:#444;text-transform:uppercase}
.site-footer{left:0;top:1087px;width:672px;height:113px;background:var(--brand);color:#fff}
.footer-title{font-size:7.5px;text-transform:uppercase}
.social{width:13px;height:13px;background:#777}
.contact-line{font-size:8px;white-space:nowrap}
.copyright{left:0;width:672px;top:1156px;font-size:5.6px;text-align:center;color:#fff}
</style>
</head>
<body>

<header class="abs site-header">
  <div class="abs brand-name">Lantern Pathway</div>
  <div class="abs header-action" style="left:427px">
    <i class="dot"><svg width="16" height="16" viewBox="0 0 16 16"><circle cx="8" cy="5" r="3.3" fill="#fff"/><path d="M2 15c0-4 3-6 6-6s6 2 6 6z" fill="#fff"/></svg></i>
    <span>REGISTER HERE</span>
  </div>
  <div class="abs header-action" style="left:477px">
    <i class="dot"><svg width="16" height="16" viewBox="0 0 16 16"><circle cx="6.5" cy="6.5" r="4" fill="none" stroke="#fff" stroke-width="2"/><path d="M9.5 9.5l4 4" stroke="#fff" stroke-width="2.4" stroke-linecap="round"/></svg></i>
    <span>SEARCH HERE</span>
  </div>
</header>

<nav class="abs main-nav">
  <div class="abs nav-home"></div>
  <div class="abs nav-item" style="left:157px">Home</div>
  <div class="abs nav-item" style="left:209px">About Us</div>
  <div class="abs nav-item" style="left:277px">Services</div>
  <div class="abs nav-item" style="left:354px">Shadow &nbsp;Support</div>
  <div class="abs nav-item" style="left:445px">For Referrers</div>
  <div class="abs nav-item" style="left:530px">Contact Us</div>
</nav>

<main>
  <div class="abs content-panel"></div>
  <div class="abs hero" role="img" aria-label="Photo of a clinician working in a laboratory"></div>
  <div class="abs slider-tab"><i></i><i></i><i></i><i></i></div>

  <section>
    <div class="abs drop" style="left:207px;top:366px">A</div>
    <div class="abs heading" style="left:238px;top:375px">bout us</div>
    <div class="abs sub" style="left:244px;top:392px">Who we are?</div>
    <p class="abs copy" style="left:170px;top:410px;width:152px"><b>Lantern Pathway</b> is part of the Meridale Therapy Group of Companies, who are providing speech language therapy, occupational therapy and educational therapy services to both the Singapore and the international school community.<br><br><b>Lantern Pathway</b> aims to work in an integrated manner, respecting the work of the respective professionals involved and collaborating effectively.</p>

    <div class="abs drop" style="left:410px;top:366px">M</div>
    <div class="abs heading" style="left:442px;top:375px">ission</div>
    <div class="abs sub" style="left:445px;top:392px">Whats our aim?</div>
    <p class="abs copy" style="left:362px;top:410px;width:154px;height:108px;overflow:hidden"><b>Lantern Pathway</b> was borne out of our Speech language Pathologists' frustration at a frequent lack of carry-over of goals to a classroom setting by external shadows. Carrying over of goals in real settings is highly important as it allows for students to generalize skills quicker. By generalizing skills, this means that the student would have truly learned a specific skill and can apply this in different settings. In the course of our work, we have often found the need to provide external shadows with further training and strategies of reporting. Lantern Pathway is committed to</p>
  </section>

  <section>
    <div class="abs drop" style="left:250px;top:533px">S</div>
    <div class="abs heading" style="left:282px;top:542px">ervices &nbsp;we offer &nbsp;you</div>
    <div class="abs sub" style="left:290px;top:562px">We provide a full fledged, seamless service that serves to</div>

    <div class="abs service-photo" style="left:170px;top:580px;background:linear-gradient(135deg,#e8e6e4,#b8b2ad)" role="img" aria-label="Photo of a therapist at work"></div>
    <div class="abs service-label" style="left:138px;top:639px">Train shadows</div>
    <p class="abs copy" style="left:142px;top:658px;width:118px">Train shadows with a strong focus on equipping them with dynamic, clinical skills.</p>

    <div class="abs service-photo" style="left:308px;top:580px;background:linear-gradient(135deg,#c9b7a6,#7d6a5c)" role="img" aria-label="Photo of a family together"></div>
    <div class="abs service-label" style="left:276px;top:639px">Provide families</div>
    <p class="abs copy" style="left:283px;top:658px;width:118px">Provide families with well-trained Shadows who are mentored by Speech Language Pathologists and Professional Therapists to carry out shadow support.</p>

    <div class="abs service-photo" style="left:446px;top:580px;background:linear-gradient(135deg,#b9d4e8,#e9ddd2)" role="img" aria-label="Photo of a professional consultation"></div>
    <div class="abs service-label" style="left:414px;top:639px">Work with educational</div>
    <p class="abs copy" style="left:420px;top:658px;width:118px">Provide families with well-trained Shadows who are mentored by Speech Language Pathologists and Professional Therapists to carry out shadow support.</p>
  </section>

  <section>
    <div class="abs drop" style="left:255px;top:706px">S</div>
    <div class="abs heading" style="left:287px;top:716px">hadow support</div>

    <div class="abs num" style="left:147px;top:758px">1</div>
    <div class="abs q-title" style="left:168px;top:763px">What is shadow support?</div>
    <p class="abs q-body" style="left:167px;top:782px;width:102px">A shadow support is para-professional who can help a struggling student to integrate and learn in their school environment.</p>

    <div class="abs num" style="left:284px;top:758px">2</div>
    <div class="abs q-title" style="left:304px;top:763px">What are its Advantages?</div>
    <p class="abs q-body" style="left:306px;top:782px;width:101px">A fully trained shadow support is an asset to the student who otherwise would have trouble fitting in and adapting to the mainstream school environment.</p>

    <div class="abs num" style="left:419px;top:758px">3</div>
    <div class="abs q-title" style="left:440px;top:763px;width:100px">How do I know if my child needs shadowing</div>
    <p class="abs q-body" style="left:439px;top:782px;width:101px">A consultation with our Speech Language Pathologist, along with an assessment by an Educational Psychologist would provide us with an indication of whether the child requires shadowing.</p>
  </section>

  <section class="abs enquiry-band">
    <div class="abs drop" style="left:190px;top:4px;width:34px;height:34px;line-height:34px">E</div>
    <div class="abs heading" style="left:224px;top:16px">nquiry</div>
    <div class="abs sub" style="left:227px;top:33px">Make An Enquiry</div>
    <div class="abs field-label" style="left:193px;top:44px">Name</div>
    <div class="abs field" style="left:193px;top:54px;width:91px;height:12px"></div>
    <div class="abs field-label" style="left:312px;top:44px">Email</div>
    <div class="abs field" style="left:312px;top:55px;width:91px;height:12px"></div>
    <div class="abs field-label" style="left:194px;top:76px">Phone</div>
    <div class="abs field" style="left:193px;top:91px;width:91px;height:12px"></div>
    <div class="abs field-label" style="left:312px;top:76px">Message</div>
    <div class="abs field" style="left:312px;top:86px;width:101px;height:20px"></div>
  </section>
  <div class="abs submit">SUBMIT</div>

  <section class="abs testimonial-band">
    <div class="abs drop" style="left:274px;top:9px">T</div>
    <div class="abs heading" style="left:306px;top:19px">estimonials</div>

    <div class="abs quote-mark" style="left:163px;top:56px">“</div>
    <p class="abs quote" style="left:174px;top:57px">Being a Quillfern partner keeps my bottomline healthy! Quillfern's heavy focus on Innovation and timely introduction of new features, keep my customers loyal to my company.</p>
    <div class="abs quote-mark" style="left:268px;top:96px">”</div>
    <div class="abs author" style="left:249px;top:109px">Daniel Crane</div>

    <div class="abs quote-mark" style="left:347px;top:56px">“</div>
    <p class="abs quote" style="left:358px;top:57px">Being a Quillfern partner keeps my bottomline healthy! Quillfern's heavy focus on Innovation and timely introduction of new features, keep my customers loyal to my company.</p>
    <div class="abs quote-mark" style="left:452px;top:96px">”</div>
    <div class="abs author" style="left:441px;top:109px">Ravi Kumar</div>
  </section>
</main>

<footer class="abs site-footer">
  <div class="abs footer-title" style="left:182px;top:13px">Follow Us</div>
  <div class="abs social" style="left:184px;top:28px"></div>
  <div class="abs social" style="left:199px;top:28px"></div>
  <div class="abs social" style="left:214px;top:28px"></div>

  <div class="abs footer-title" style="left:413px;top:13px">Contact Us</div>
  <svg class="abs" style="left:411px;top:35px" width="10" height="10" viewBox="0 0 10 10"><circle cx="5" cy="5" r="4.4" fill="none" stroke="#fff" stroke-width=".8"/><path d="M3.3 2.8l1 .9-.5.8c.4.8.9 1.3 1.7 1.7l.8-.5.9 1-.8.8C5 7.3 2.7 5 2.5 3.6z" fill="#fff"/></svg>
  <div class="abs contact-line" style="left:428px;top:33px">+65 6100 4821</div>
  <svg class="abs" style="left:411px;top:47px" width="10" height="10" viewBox="0 0 10 10"><circle cx="5" cy="5" r="4.4" fill="none" stroke="#fff" stroke-width=".8"/><rect x="2.6" y="3.4" width="4.8" height="3.4" fill="#fff"/><path d="M2.6 3.4L5 5.4l2.4-2" fill="none" stroke="#7d0a0a" stroke-width=".5"/></svg>
  <div class="abs contact-line" style="left:428px;top:45px">enquiries@meridaletherapy.sg</div>
</footer>
<div class="abs copyright">© Copyright 2014 Quillfern Systems Pvt. Ltd. All Rights Reserved</div>

</body>
</html>
```